New Interrior Decoration company needs new website

We need a website for our new company specialising in interior decoration to residential and commercial markets.
We supply and install decorative and printed films for office and home decoration such as feature walls.
We would like to keep the design simple and clean.

Target Market(s)

Architects and interior designaers

Industry/Entity Type

It Company

Number of Pages Required

5+ page

Font styles to use
Sans Serif

Requirements
Must have
• Home page,
• Services/products page (split into commercial and residential)
• Gallery (split into commercial and residential)
• contact form and page
Nice to have
• Very clean and minimalistic design.

```html
<!DOCTYPE html>
<html lang="en">
<head>
<meta charset="UTF-8">
<title>Lumen Interiors</title>
<link href="https://fonts.googleapis.com/css2?family=Raleway:wght@400;500;600&family=Open+Sans:wght@400;600;700&display=swap" rel="stylesheet">
<style>
:root{
  --blue:#0a5bbd;
  --ink:#2e2e2e;
  --body:#6b6b6b;
  --white:#ffffff;
  --beige:#d4d2ae;
  --footer:#3b3b3b;
  --footer-deep:#2c2c2c;
  --field:#545454;
}
*{margin:0;padding:0;box-sizing:border-box}
html,body{width:1200px;height:2848px;overflow:hidden}
body{font-family:"Open Sans",Arial,sans-serif;color:var(--ink);background:var(--white);position:relative}
.heading{font-family:"Raleway",Arial,sans-serif;font-weight:400}
.accent{color:var(--blue)}
.btn{display:inline-block;background:var(--blue);color:var(--white);font-family:"Raleway",Arial,sans-serif;font-size:19px;text-transform:uppercase;padding:0 26px;height:50px;line-height:50px;border-radius:3px}

/* header */
.site-header{position:absolute;top:0;left:0;width:1200px;height:104px}
.brand{position:absolute;left:78px;top:30px;display:flex;align-items:center;gap:12px}
.brand-mark{width:52px;height:52px;background:var(--blue)}
.brand-name{font-family:"Raleway",Arial,sans-serif;font-weight:600;font-size:30px;line-height:30px;color:var(--ink);letter-spacing:.5px;text-transform:uppercase;width:260px}
.main-nav{position:absolute;top:32px;left:490px;display:flex}
.main-nav a{font-family:"Raleway",Arial,sans-serif;font-size:21px;color:var(--ink);text-decoration:none;height:45px;line-height:45px;padding:0 19px;margin-right:16px}
.main-nav a.active{background:var(--blue);color:var(--white);padding:0 19px}

/* hero */
.hero{position:absolute;top:104px;left:0;width:1200px;height:574px;background:linear-gradient(120deg,#5c5149 0%,#8d8b86 35%,#c9cac7 60%,#9fa5a6 80%,#6f6a62 100%)}

/* call band */
.call-band{position:absolute;top:678px;left:0;width:1200px;height:135px;background:var(--blue);display:flex;align-items:center;justify-content:center;color:var(--white);gap:16px}
.call-label{font-family:"Raleway",Arial,sans-serif;font-size:33px}
.call-number{font-size:32px;font-weight:700}
.call-or{font-family:"Raleway",Arial,sans-serif;font-size:33px;margin:0 14px}
.call-btn{background:var(--white);color:var(--ink);font-weight:700;font-size:22px;width:198px;height:57px;line-height:57px;padding-left:24px;border-radius:3px;text-transform:uppercase}

/* welcome */
.welcome{position:absolute;top:813px;left:0;width:1200px;height:336px;text-align:center}
.welcome h1{font-size:41px;margin-top:50px;text-transform:uppercase;letter-spacing:.5px}
.welcome p{width:860px;margin:26px auto 0;font-size:15px;line-height:25px;color:var(--body)}
.welcome .btn{margin-top:24px}

/* residential */
.residential{position:absolute;top:1149px;left:0;width:1200px;height:370px;background:var(--beige)}
.residential-photo{position:absolute;left:0;top:0;width:526px;height:370px;background:linear-gradient(180deg,#75714f 0%,#8a8660 55%,#b5b28e 80%,#d7d6c7 100%)}
.residential-copy{position:absolute;left:601px;top:40px;width:510px}
.residential-copy h2{font-size:41px}
.section-text{font-size:15px;line-height:25px;color:var(--body);margin-top:22px}
.residential-copy .btn{margin-top:26px}

/* commercial */
.commercial{position:absolute;top:1519px;left:0;width:1200px;height:380px}
.commercial-photo{position:absolute;inset:0;background:linear-gradient(180deg,#3e3f3e 0%,#4d4f4e 45%,#6b6d6c 68%,#cfd3d3 74%,#eef0f0 100%)}
.commercial-copy{position:absolute;left:78px;top:52px;width:510px;color:var(--white)}
.commercial-copy h2{font-size:41px}
.commercial-copy .section-text{color:#e9e9e9}
.commercial-copy .btn{margin-top:26px}

/* gallery */
.gallery{position:absolute;top:1899px;left:0;width:1200px;height:611px;text-align:center}
.gallery h2{font-size:41px;margin-top:50px;text-transform:uppercase}
.gallery-grid{position:absolute;left:78px;top:123px;width:1044px;display:grid;grid-template-columns:repeat(4,234px);column-gap:37px;row-gap:21px}
.gallery-item{height:157px}
.g1{background:linear-gradient(135deg,#2b2622,#6d5f52)}
.g2{background:linear-gradient(135deg,#5a2a1c,#b8a4b8)}
.g3{background:linear-gradient(135deg,#8c9089,#5e6a62)}
.g4{background:linear-gradient(135deg,#9a3a27,#7a7d80)}
.g5{background:linear-gradient(135deg,#c04060,#3f6fa4)}
.g6{background:linear-gradient(135deg,#3a9aa0,#8fd0d2)}
.g7{background:linear-gradient(135deg,#d3b65a,#c2392b)}
.g8{background:linear-gradient(135deg,#d9dcdc,#6e5a45)}
.gallery .btn{position:absolute;left:526px;top:465px;width:149px;padding:0}

/* footer */
.site-footer{position:absolute;top:2510px;left:0;width:1200px;height:285px;background:var(--footer);color:var(--white)}
.footer-col{position:absolute;top:38px}
.footer-about{left:78px;width:240px}
.footer-brand{display:flex;align-items:center;gap:8px}
.footer-brand .brand-mark{width:36px;height:36px}
.footer-brand .brand-name{font-size:20px;line-height:20px;color:var(--white);width:170px}
.footer-about p{font-size:15px;line-height:25px;margin-top:18px}
.footer-col h3{font-family:"Raleway",Arial,sans-serif;font-weight:400;font-size:23px;margin-bottom:14px}
.footer-links{left:349px}
.footer-links ul{list-style:none}
.footer-links li{font-size:17px;height:37px;display:flex;align-items:center;gap:10px}
.footer-contact{left:621px;width:240px}
.contact-row{display:flex;gap:12px;font-size:14px;line-height:25px;margin-bottom:12px}
.contact-row svg{flex:none;margin-top:4px}
.contact-row strong{font-weight:700}
.social{display:flex;gap:20px;margin-top:8px}
.social span{width:46px;height:46px;border:2px solid var(--white);border-radius:3px;display:block}
.social span:first-child{background:var(--white)}
.footer-news{left:891px;width:232px}
.field{height:38px;background:var(--field);font-size:14px;line-height:38px;padding-left:10px;margin-bottom:14px;color:#e6e6e6}
.footer-news .btn{height:46px;line-height:46px;font-size:18px;padding:0 22px}
.footer-bar{position:absolute;top:2795px;left:0;width:1200px;height:53px;background:var(--footer-deep);color:var(--white);text-align:center;font-size:15px;line-height:53px}
</style>
</head>
<body>

<header class="site-header">
  <div class="brand"><span class="brand-mark"></span><span class="brand-name">Lumen Interiors</span></div>
  <nav class="main-nav">
    <a class="active">HOME</a><a>ABOUT</a><a>SERVICES</a><a>GALLERY</a><a>CONTACT</a>
  </nav>
</header>

<div class="hero" role="img" aria-label="Modern open-plan kitchen and dining room with white table, black chairs and globe pendant lights"></div>

<section class="call-band">
  <span class="call-label">CALL US NOW!</span>
  <svg width="64" height="64" viewBox="0 0 64 64" aria-hidden="true"><circle cx="32" cy="32" r="30" fill="none" stroke="#fff" stroke-width="2"/><path d="M24 18c2 0 3 4 4 6s-2 3-2 4c1 3 5 7 8 8 1 0 2-3 4-2s6 2 6 4-3 6-6 6C27 44 20 37 20 24c0-3 2-6 4-6z" fill="#fff"/></svg>
  <span class="call-number">123 456 7890</span>
  <span class="call-or">OR</span>
  <span class="call-btn">Contact Us</span>
</section>

<section class="welcome">
  <h1 class="heading">Welcome to <span class="accent">Lumen Interiors</span></h1>
  <p>Lorem Ipsum is simply dummy text of the printing and typesetting industry. Lorem Ipsum has been the industry's standard dummy text ever since the 1500s, when an unknown printer took a galley of type and scrambled it to make a type specimen book.</p>
  <span class="btn">Read More</span>
</section>

<section class="residential">
  <div class="residential-photo" role="img" aria-label="Living room feature wall with textured olive wallcovering, low sideboard, framed art and vases"></div>
  <div class="residential-copy">
    <h2 class="heading">Residential <span class="accent">Interiors</span></h2>
    <p class="section-text">Lorem Ipsum is simply dummy text of the printing and typesetting industry. Lorem Ipsum has been the industry's standard dummy text ever since the 1500s, when an unknown printer took a galley of type and scrambled it to make a type specimen book.</p>
    <span class="btn">Read More</span>
  </div>
</section>

<section class="commercial">
  <div class="commercial-photo" role="img" aria-label="Dark concrete-look feature wall with a white sofa on a pale floor"></div>
  <div class="commercial-copy">
    <h2 class="heading">Commercial Interiors</h2>
    <p class="section-text">Lorem Ipsum is simply dummy text of the printing and typesetting industry. Lorem Ipsum has been the industry's standard dummy text ever since the 1500s, when an unknown printer took a galley of type and scrambled it to make a type specimen book.</p>
    <span class="btn">Read More</span>
  </div>
</section>

<section class="gallery">
  <h2 class="heading">Latest <span class="accent">Gallery</span></h2>
  <div class="gallery-grid">
    <div class="gallery-item g1" role="img" aria-label="Dark lounge interior"></div>
    <div class="gallery-item g2" role="img" aria-label="Lounge chair before a rust-toned wall"></div>
    <div class="gallery-item g3" role="img" aria-label="Stone-effect corridor wall"></div>
    <div class="gallery-item g4" role="img" aria-label="Brick-effect office feature wall"></div>
    <div class="gallery-item g5" role="img" aria-label="Colourful printed graphic wall"></div>
    <div class="gallery-item g6" role="img" aria-label="Turquoise dotted window film"></div>
    <div class="gallery-item g7" role="img" aria-label="Wood-panel wall with red chairs"></div>
    <div class="gallery-item g8" role="img" aria-label="Curved reception counter"></div>
  </div>
  <span class="btn">View All</span>
</section>

<footer class="site-footer">
  <div class="footer-col footer-about">
    <div class="footer-brand"><span class="brand-mark"></span><span class="brand-name">LUMEN INTERIORS</span></div>
    <p>Lorem Ipsum is simply dummy text of the printing and typesetting industry. Lorem Ipsum has been the industry's standard dummy text ever since the 1500.</p>
  </div>
  <div class="footer-col footer-links">
    <h3>Useful Links</h3>
    <ul>
      <li><svg width="22" height="10" viewBox="0 0 22 10" aria-hidden="true"><path d="M0 5h19M15 1l5 4-5 4" stroke="#fff" stroke-width="2" fill="none"/></svg>Home</li>
      <li><svg width="22" height="10" viewBox="0 0 22 10" aria-hidden="true"><path d="M0 5h19M15 1l5 4-5 4" stroke="#fff" stroke-width="2" fill="none"/></svg>About</li>
      <li><svg width="22" height="10" viewBox="0 0 22 10" aria-hidden="true"><path d="M0 5h19M15 1l5 4-5 4" stroke="#fff" stroke-width="2" fill="none"/></svg>Services</li>
      <li><svg width="22" height="10" viewBox="0 0 22 10" aria-hidden="true"><path d="M0 5h19M15 1l5 4-5 4" stroke="#fff" stroke-width="2" fill="none"/></svg>Gallery</li>
      <li><svg width="22" height="10" viewBox="0 0 22 10" aria-hidden="true"><path d="M0 5h19M15 1l5 4-5 4" stroke="#fff" stroke-width="2" fill="none"/></svg>Contact</li>
    </ul>
  </div>
  <div class="footer-col footer-contact">
    <h3>Get In Touch</h3>
    <div class="contact-row"><svg width="14" height="20" viewBox="0 0 14 20" aria-hidden="true"><path d="M7 0a7 7 0 0 1 7 7c0 5-7 13-7 13S0 12 0 7a7 7 0 0 1 7-7z" fill="#fff"/><circle cx="7" cy="7" r="2.6" fill="#3b3b3b"/></svg><span>Lorem Ipsum is dummy text of the printing.</span></div>
    <div class="contact-row"><svg width="16" height="16" viewBox="0 0 16 16" aria-hidden="true"><path d="M3 0c1 0 2 3 2 4s-1 2-1 2c1 2 3 4 5 5 0 0 1-1 2-1s4 1 4 2-2 4-4 4C6 16 0 10 0 4 0 2 2 0 3 0z" fill="#fff"/></svg><strong>123 456 7890</strong></div>
    <div class="contact-row"><svg width="18" height="14" viewBox="0 0 18 14" aria-hidden="true"><rect x="1" y="1" width="16" height="12" fill="none" stroke="#fff" stroke-width="1.6"/><path d="M1 1l8 7 8-7" fill="none" stroke="#fff" stroke-width="1.6"/></svg><span>info@lumeninteriors.com</span></div>
    <div class="social"><span></span><span></span><span></span></div>
  </div>
  <div class="footer-col footer-news">
    <h3>Newsletter</h3>
    <div class="field">Enter Name</div>
    <div class="field">Enter Email</div>
    <span class="btn">Subscribe</span>
  </div>
</footer>
<div class="footer-bar">© <strong>LUMEN INTERIORS</strong> - 2016. All Rights Reserved.</div>

</body>
</html>
```